Sell the dream! Property investment proposal document

We are looking for a proposal document which outlines our vision for property development. The purpose of the document is to raise investment from investors - sell the dream!
Brief summary:
Kestrel Dwellings Developments, is an emerging New Zealand property investment company with a focus on providing unique property investment opportunities.
Our expertise and capabilities in architectural modular homes provide us with a remarkable advantage in tackling the development of properties that are typically considered challenging, remote, or uniquely positioned.
Our specialization in this niche sector of property development not only sets us apart from competitors, but also paves the way for lucrative investment opportunities in the New Zealand property market.
Feel free to use any images from www.kestreldwellings.co.nz
Target Market(s)
investors for a unique property development opportunity
Industry/Entity Type
luxury property development in unique locations throughout New Zealand
Colors
Designer to choose only greyscale colors for use in the design.
Look and feel

```html
<!DOCTYPE html>
<html lang="en">
<head>
<meta charset="utf-8">
<title>Kestrel Dwellings Developments – Investment Proposal</title>
<link href="https://fonts.googleapis.com/css2?family=Montserrat:wght@400;500;700;800&display=swap" rel="stylesheet">
<style>
  :root {
    --backdrop: #666666;
    --page: #f4f5f7;
    --ink: #111111;
    --ink-soft: #231f20;
    --body: #2a2a2a;
    --photo-top: #9fb4c9;
    --photo-bottom: #7d8271;
  }
  * { margin: 0; padding: 0; box-sizing: border-box; }
  html, body { width: 877px; height: 1200px; overflow: hidden; }
  body {
    position: relative;
    background: var(--backdrop);
    font-family: "Montserrat", sans-serif;
    color: var(--ink);
  }
  .page { position: absolute; background: var(--page); }
  .page--cover { left: 20px; top: 16px; width: 409px; height: 578px; }
  .page--overview { left: 21px; top: 608px; width: 406px; height: 574px; }
  .page--finance { left: 449px; top: 313px; width: 406px; height: 574px; }

  .cover-photo {
    position: absolute; left: 131px; top: 16px; width: 298px; height: 375px;
    background: linear-gradient(180deg, var(--photo-top) 0%, var(--photo-bottom) 100%);
  }
  .brand-vertical {
    position: absolute; left: 44px; top: 16px; width: 78px; height: 375px;
    writing-mode: vertical-rl; transform: rotate(180deg);
    font-size: 84px; font-weight: 500; line-height: 78px;
    color: var(--ink-soft); letter-spacing: -1px;
    white-space: nowrap;
  }
  .cover-title {
    position: absolute; left: 49px; top: 421px;
    font-size: 31px; font-weight: 800; line-height: 37px; letter-spacing: 0.3px;
  }
  .cover-lede {
    position: absolute; left: 49px; top: 508px;
    font-size: 10.6px; font-weight: 400; line-height: 19.5px; text-transform: uppercase;
  }

  .heading {
    position: absolute; font-size: 16px; font-weight: 800; line-height: 18px;
    text-transform: uppercase; white-space: nowrap;
  }
  .copy {
    position: absolute; font-size: 5.4px; font-weight: 400; color: var(--body);
    white-space: nowrap;
  }
  .col-left { left: 49px; }
  .col-left-inset { left: 50px; }
  .col-right { left: 477px; }
  .lh-14 { line-height: 14px; }
  .lh-15 { line-height: 14.8px; }
  .lh-12 { line-height: 11.7px; }
  .lh-145 { line-height: 14.5px; }
  .lh-16 { line-height: 16.4px; }
</style>
</head>
<body>

  <section class="page page--cover"></section>
  <div class="cover-photo" role="img" aria-label="Photograph of a modern modular home with a sea view, lawn in the foreground"></div>
  <div class="brand-vertical">Kestrel</div>
  <h1 class="cover-title">WELCOME TO<br>KESTREL</h1>
  <p class="cover-lede">Lorem ipsum dolor sit amet, consectetur<br>adipiscing elit, sed do eiusmod tempor incididunt<br>ut labore et dolore magna aliqua.</p>

  <section class="page page--overview"></section>
  <h2 class="heading col-left" style="top:632px">Business Overview</h2>
  <p class="copy col-left lh-14" style="top:659px">Kestrel Dwellings Developments, is an emerging New Zealand property investment company with a focus on providing unique<br>property investment opportunities.</p>
  <p class="copy col-left lh-14" style="top:700px">Our expertise and capabilities in architectural modular homes provide us with a remarkable advantage in tackling the develop-<br>ment of properties that are typically considered challenging, remote, or uniquely positioned.</p>
  <p class="copy col-left lh-14" style="top:742px">As a company, with 48 employees boasting a wealth of experience in handling complex architectural projects, making us<br>well-equipped to navigate the intricacies and demands of such ventures. This advantage allows us to not only execute projects<br>efficiently but also to deliver exceptional results within condensed time frames.</p>
  <p class="copy col-left lh-14" style="top:798px">By capitalizing on our ability to develop difficult, remote, or one-of-a-kind properties swiftly and effectively, Kestrel Dwellings Devel-<br>opments offers investors a rare chance to engage in projects that promise exceptional profitability in the New Zealand property<br>market.</p>
  <p class="copy col-left lh-14" style="top:854px">Our specialization in this niche sector of property development not only sets us apart from competitors, but also paves the way<br>for lucrative investment opportunities in the New Zealand property market.</p>

  <h2 class="heading col-left" style="top:895px">Business Origins</h2>
  <p class="copy col-left-inset lh-15" style="top:924px">Kestrel Dwellings Developments was established with the goal of transforming the property investment market in<br>New Zealand by introducing an innovative approach that centers on architectural modular designs and streamlined<br>project timelines.</p>
  <p class="copy col-left-inset lh-15" style="top:983px">Driven by our enthusiasm for architecture and real estate, we have expanded our successful business model to not only<br>offer financial opportunities for investors but also to expand on our passion for high-end architectural design.</p>
  <p class="copy col-left-inset lh-15" style="top:1027px">With a wealth of experience accumulated over the past six years in the construction and the property market, we are<br>pivoting to focus solely on our property development initiatives,</p>
  <p class="copy col-left-inset lh-15" style="top:1071px">presenting completed Kestrel projects to the market, in exclusive locations. These projects will boast high-quality<br>standards, meticulous attention to detail and landscaping, and creative design elements.</p>
  <p class="copy col-left-inset lh-15" style="top:1116px">By introducing completed Kestrel properties into the market, we aim to reach a wider audience, catering to individuals<br>who prefer ready-to-occupy homes, over engaging in the design and</p>

  <section class="page page--finance"></section>
  <p class="copy col-right lh-12" style="top:334px">construction process. This approach also simplifies the financing process for prospective buyers, as established properties are<br>often preferred by financial lenders.</p>
  <h2 class="heading col-right" style="top:372px">Competitive Advantage</h2>
  <p class="copy col-right lh-145" style="top:397px">Our competitive advantage lies in the uniqueness of our property investment opportunities. Unlike traditional real estate com-<br>panies, we focus on offering properties that are not only profitable but also aesthetically pleasing and unique. By catering to the<br>tastes of architecture lovers, we set ourselves apart from the competition and attract a niche market of customers who appreci-<br>ate the artistry and design of our projects.</p>
  <p class="copy col-right lh-145" style="top:469px">Additionally, the streamlined and condensed timelines facilitated by our modular approach<br>provide quicker returns on investment.</p>
  <h2 class="heading col-right" style="top:518px">Financial Summary</h2>
  <p class="copy col-right lh-16" style="top:545px">In terms of financial projections, with each development, we anticipate a profit of 10%-20% which will be project dependent.</p>
  <p class="copy col-right lh-16" style="top:578px">This growth is fueled by the increasing demand for unique property investments in New Zealand and our ability to deliver<br>high-quality services to the market in a condensed time frame, with heavily controlled costs</p>
  <p class="copy col-right lh-16" style="top:627px">With a solid business model and a dedicated team, we are confident in our ability to achieve success and establish Kestrel Dwellings<br>Investments as a trusted name in the industry.</p>
  <p class="copy col-right lh-16" style="top:676px">New Zealand's property market has been experiencing steady growth over the years, making it an attractive destination for<br>property investors. With its beautiful landscapes and strong economy, New Zealand offers a diverse range of investment oppor-<br>tunities for both<br>local and international investors. The demand for quality properties in prime locations continues to rise, creating a favorable envi-<br>ronment for property investment companies like ours that can lean on our modular benefits of being able to reach unique and<br>remote</p>

</body>
</html>
```